SEO Friendly Web Design Needed for Leading Software Company

Founded in 1986, TRBW is the market leader for innovative software solutions for the heavy civil construction industry. Our suite of products, including the bestsellers GroundQuote® and SiteTrack®, are used by more than 40,000 workers every day to improve their proficiency at estimating, job management, resource management, safety and equipment maintenance. TRBW also offers new mobile applications and cloud computing services so companies can work on a wide array of devices including laptops, tablets and smartphones.

In addition to high quality software, TRBW is best known for providing world-class customer service, and for its friendly, employee-ownership culture. We offer a full range of professional support options to help customers maximize their software investment including implementation planning, training and INSTANT 24/7 phone support.

Goals, objectives and target audience

The goal of our new layout and design will be to increase conversions, enhance user experience and enhance our SERP rankings.

Our objectives are as follows:
1. Clean and well laid out home page. White space is OK.
2. CTAs in strategic locations throughout to drive conversions and MQLs
3. SEO rich content with appropriate layout to meet our SEO requirements
4. 2 Master Design Templates – Home & Internal
5. Custom Design elements for individual modules

Target Audience:
- Heavy / Civil Construction Industry
- C Level executives or persons in leadership roles who utilize our software
- MEN in the construction industry.

Requirements
Should not have
• Feminine design - our industry is largely male construction workers.
Don't use script or goofy fonts
Don't change the logo, or put it in an image where it is not easily viewable.

```html
<!DOCTYPE html>
<html lang="en">
<head>
<meta charset="utf-8">
<title>TRBW – Construction Software</title>
<link rel="stylesheet" href="https://fonts.googleapis.com/css2?family=Roboto:wght@300;400;500;700&display=swap">
<style>
:root{
  --green:#1fa24a;
  --green-dark:#16823a;
  --orange:#f5821f;
  --ink:#1d1d1d;
  --muted:#666;
  --line:#dcdcdc;
  --topbar:#3a3a3a;
  --footer:#2b2a22;
  --footer-text:#d8d8d0;
  --hero-a:#f2f2f2;
  --hero-b:#e4e4e4;
  --grey-btn:#8c8c8c;
}
*{box-sizing:border-box;margin:0;padding:0}
html,body{width:1200px;height:3794px;overflow:hidden}
body{font-family:"Roboto",Arial,sans-serif;color:var(--ink);background:#fff;position:relative}
ul{list-style:none}
a{color:inherit;text-decoration:none}

.topbar{height:26px;background:var(--topbar);color:#eee;font-size:11px;display:flex;align-items:center;justify-content:space-between;padding:0 95px}
.topbar nav a{margin-right:14px}
.topbar .phone{color:var(--orange);font-weight:700;font-size:13px;margin-left:10px}

.header{height:107px;display:flex;align-items:center;justify-content:space-between;padding:0 92px 0 95px;border-bottom:1px solid #e6e6e6}
.brand{display:flex;align-items:center;gap:12px;font-size:40px;font-weight:700;color:var(--green);letter-spacing:1px}
.brand-square{width:34px;height:34px;background:var(--green)}
.main-nav a{font-size:18px;color:#777;margin-left:26px}
.main-nav a.active{color:var(--orange)}

.hero{height:505px;background:linear-gradient(180deg,var(--hero-a),var(--hero-b));position:relative}
.hero-copy{position:absolute;left:95px;top:62px;width:560px}
.hero h1{font-size:46px;font-weight:700;letter-spacing:-1px}
.hero .lead{font-size:17px;font-weight:500;margin-top:18px;line-height:1.35;color:#333}
.hero-list{margin-top:16px}
.hero-list li{font-size:13px;padding:12px 0 13px 22px;border-top:1px solid #cfcfcf;position:relative}
.tick{position:absolute;left:3px;width:6px;height:11px;border:solid #222;border-width:0 2px 2px 0;transform:rotate(40deg)}
.hero-list .tick{top:12px}
.hero-ctas{position:absolute;left:95px;top:398px;display:flex;gap:24px}
.btn{display:inline-flex;align-items:center;color:#fff;font-weight:700;clip-path:polygon(0 0,90% 0,100% 50%,90% 100%,0 100%)}
.btn-lg{height:36px;font-size:15px;padding:0 34px 0 16px}
.btn-green{background:var(--green)}
.btn-grey{background:var(--grey-btn)}
.btn .arr{margin-left:10px;font-size:13px}

.tiles{position:absolute;left:712px;top:41px;display:grid;grid-template-columns:repeat(3,124px);grid-auto-rows:145px;gap:8px}
.tile{background:#fff;border:1px solid #ddd;padding:4px;text-align:center;font-size:11px;color:#333;display:flex;flex-direction:column}
.tile .pic{height:92px}
.tile span{margin-top:6px;line-height:1.2}
.tile.active{background:var(--orange);color:#fff;border-color:var(--orange)}

.products{padding-top:87px}
.product{height:414px;position:relative;margin:0 95px}
.product .photo{position:absolute;left:7px;top:0;width:400px;height:325px;border:6px solid #fff;box-shadow:0 1px 6px rgba(0,0,0,.25)}
.product .info{position:absolute;left:449px;top:30px;width:560px}
.product h2{font-size:37px;font-weight:300;color:var(--orange)}
.product ul{margin-top:14px}
.product li{font-size:13px;font-weight:700;line-height:1.6;padding:8px 0 10px 24px;border-bottom:1px solid var(--line);position:relative}
.product li .tick{top:12px}
.product .ctas{display:flex;gap:8px;margin-top:20px}
.btn-sm{height:20px;font-size:10px;padding:0 20px 0 8px;font-weight:500}

.to-top{position:absolute;right:0;top:996px;width:69px;height:43px;background:var(--green);color:#fff;font-size:9px;font-weight:700;display:flex;align-items:center;justify-content:center;text-align:center;line-height:1.1}

.footer{position:absolute;left:0;top:3247px;width:1200px;height:496px;background:linear-gradient(180deg,#4a4a36,var(--footer) 45%,#3b3a2c);color:var(--footer-text)}
.footer-tab{position:absolute;left:562px;top:0;width:72px;height:40px;background:#fff;display:flex;align-items:center;justify-content:center;color:var(--green);font-weight:700;font-size:16px}
.footer-cols{position:absolute;left:95px;top:98px;display:grid;grid-template-columns:206px 210px 211px 202px 180px}
.footer h3{color:var(--orange);font-size:16px;font-weight:500;padding-bottom:9px;border-bottom:1px solid rgba(255,255,255,.2);width:160px;margin-bottom:8px}
.footer h3.sub{margin-top:16px}
.footer li{font-size:11px;height:30px;display:flex;align-items:center;padding-left:10px;position:relative}
.footer li::before{content:"";position:absolute;left:0;width:3px;height:3px;background:var(--footer-text)}
.footer li.active{background:#fff;color:var(--ink);width:150px}
.contact li{padding-left:0}
.contact li::before{display:none}
.contact li b{font-weight:400;width:56px}
.contact .addr{height:40px;line-height:1.3}
.social{display:flex;gap:8px;margin-top:6px}
.social span{width:26px;height:26px;border:2px solid var(--footer-text);border-radius:50%}

.bottombar{position:absolute;left:0;top:3743px;width:1200px;height:51px;background:var(--green);color:#fff;font-size:11px;display:flex;align-items:center;padding:0 95px;gap:20px}
</style>
</head>
<body>

<header>
  <div class="topbar">
    <nav><a href="#">Tools</a><a href="#">News</a><a href="#">Blogs</a></nav>
    <div><a href="#">Contact Us</a> &nbsp;&nbsp; <a href="#">Sales</a> | <span class="phone">1800 555 0142</span></div>
  </div>
  <div class="header">
    <a class="brand" href="#"><span class="brand-square"></span>TRBW</a>
    <nav class="main-nav">
      <a class="active" href="#">Software</a><a href="#">Services</a><a href="#">Pricing</a><a href="#">Careers</a><a href="#">Events</a><a href="#">About Us</a>
    </nav>
  </div>
</header>

<section class="hero">
  <div class="hero-copy">
    <h1>Construction Software</h1>
    <p class="lead">The Industry leader in Construction Software that can manage your projects from start to finish</p>
    <ul class="hero-list">
      <li><i class="tick"></i>Lorem ipsum dolor sit amet, consectetur sed eiusmod incididunt</li>
      <li><i class="tick"></i>Lorem ipsum dolor sit amet, consectetur adipisicing eiusmod tempor</li>
      <li><i class="tick"></i>Amet, consectetur adipisicing elit, lorem ipsum dolor sit amet</li>
      <li><i class="tick"></i>Consectetur sed eiusmod incididunt lorem ipsum consectetur sed</li>
    </ul>
  </div>
  <div class="hero-ctas">
    <a class="btn btn-lg btn-green" href="#">Contact Sales <span class="arr">›</span></a>
    <a class="btn btn-lg btn-green" href="#">View Demo <span class="arr">›</span></a>
  </div>
  <div class="tiles">
    <a class="tile active" href="#"><div class="pic" role="img" aria-label="Excavator on a construction site" style="background:linear-gradient(#c9b46a,#7a6a3a)"></div><span>Estimating &amp; Bidding</span></a>
    <a class="tile" href="#"><div class="pic" role="img" aria-label="Team in suits and hard hats" style="background:linear-gradient(#cfd4d8,#3a3d42)"></div><span>Job Management</span></a>
    <a class="tile" href="#"><div class="pic" role="img" aria-label="Worker in a truck cab" style="background:linear-gradient(#e8ecef,#8b97a0)"></div><span>Dispatching &amp; Scheduling</span></a>
    <a class="tile" href="#"><div class="pic" role="img" aria-label="Worker in safety gear" style="background:linear-gradient(#8fb2d8,#b0582e)"></div><span>Safety Management</span></a>
    <a class="tile" href="#"><div class="pic" role="img" aria-label="Survey GPS rover on a tripod" style="background:linear-gradient(#7fa7cf,#a88a52)"></div><span>GPS</span></a>
    <a class="tile" href="#"><div class="pic" role="img" aria-label="Hand tools" style="background:linear-gradient(#f2f2f2,#c9a24a)"></div><span>Equipment Maintenance</span></a>
    <a class="tile" href="#"><div class="pic" role="img" aria-label="Fuel storage tanks" style="background:linear-gradient(#a9c2d8,#8a8a86)"></div><span>Fuel Tracking</span></a>
    <a class="tile" href="#"><div class="pic" role="img" aria-label="Smartphone devices" style="background:linear-gradient(#e0e4e8,#4a5058)"></div><span>Mobile Apps</span></a>
    <a class="tile" href="#"><div class="pic" role="img" aria-label="Bridge under construction" style="background:linear-gradient(#d7c9a6,#6e6452)"></div><span>Software Keyword Text</span></a>
  </div>
</section>

<main class="products">
  <article class="product">
    <div class="photo" role="img" aria-label="Engineer with plans in front of an excavator" style="background:linear-gradient(160deg,#b8c2c8,#c8a23c 60%,#6a5a3a)"></div>
    <div class="info">
      <h2>Estimating &amp; Bidding</h2>
      <ul>
        <li><i class="tick"></i>Lorem ipsum dolor sit amet, consectetur adipisicing elit, sed do eiusmod tempor incididunt</li>
        <li><i class="tick"></i>Lorem ipsum dolor sit amet, consectetur adipisicing elit,</li>
        <li><i class="tick"></i>Lorem ipsum dolor sit amet, consectetur adipisicing elit, sed do eiusmod tempor incididunt</li>
        <li><i class="tick"></i>Sed do eiusmod tempor incididunt ut labore et dolore magna aliqua</li>
      </ul>
      <div class="ctas"><a class="btn btn-sm btn-green" href="#">Contact Sales ›</a><a class="btn btn-sm btn-grey" href="#">Read More ›</a></div>
    </div>
  </article>
  <article class="product">
    <div class="photo" role="img" aria-label="Managers in suits and hard hats on site" style="background:linear-gradient(160deg,#d8dde0,#7b8188 55%,#2a2c30)"></div>
    <div class="info">
      <h2>Job Management</h2>
      <ul>
        <li><i class="tick"></i>Lorem ipsum dolor sit amet, consectetur adipisicing elit, sed do eiusmod tempor incididunt</li>
        <li><i class="tick"></i>Lorem ipsum dolor sit amet, consectetur adipisicing elit,</li>
        <li><i class="tick"></i>Lorem ipsum dolor sit amet, consectetur adipisicing elit, sed do eiusmod tempor incididunt</li>
        <li><i class="tick"></i>Sed do eiusmod tempor incididunt ut labore et dolore magna aliqua</li>
      </ul>
      <div class="ctas"><a class="btn btn-sm btn-green" href="#">Contact Sales ›</a><a class="btn btn-sm btn-grey" href="#">Read More ›</a></div>
    </div>
  </article>
  <article class="product">
    <div class="photo" role="img" aria-label="Driver in a hard hat at a truck window" style="background:linear-gradient(160deg,#f2f4f5,#c8d0d6 55%,#8a949c)"></div>
    <div class="info">
      <h2>Dispatching &amp; Scheduling</h2>
      <ul>
        <li><i class="tick"></i>Lorem ipsum dolor sit amet, consectetur adipisicing elit, sed do eiusmod tempor incididunt</li>
        <li><i class="tick"></i>Lorem ipsum dolor sit amet, consectetur adipisicing elit,</li>
        <li><i class="tick"></i>Lorem ipsum dolor sit amet, consectetur adipisicing elit, sed do eiusmod tempor incididunt</li>
        <li><i class="tick"></i>Sed do eiusmod tempor incididunt ut labore et dolore magna aliqua</li>
      </ul>
      <div class="ctas"><a class="btn btn-sm btn-green" href="#">Contact Sales ›</a><a class="btn btn-sm btn-grey" href="#">Read More ›</a></div>
    </div>
  </article>
  <article class="product">
    <div class="photo" role="img" aria-label="Worker in hard hat and ear protection" style="background:linear-gradient(160deg,#7eaee0,#a9c6e4 45%,#b4512a 75%,#33384a)"></div>
    <div class="info">
      <h2>Safety Management</h2>
      <ul>
        <li><i class="tick"></i>Lorem ipsum dolor sit amet, consectetur adipisicing elit, sed do eiusmod tempor incididunt</li>
        <li><i class="tick"></i>Lorem ipsum dolor sit amet, consectetur adipisicing elit,</li>
        <li><i class="tick"></i>Lorem ipsum dolor sit amet, consectetur adipisicing elit, sed do eiusmod tempor incididunt</li>
        <li><i class="tick"></i>Sed do eiusmod tempor incididunt ut labore et dolore magna aliqua</li>
      </ul>
      <div class="ctas"><a class="btn btn-sm btn-green" href="#">Contact Sales ›</a><a class="btn btn-sm btn-grey" href="#">Read More ›</a></div>
    </div>
  </article>
  <article class="product">
    <div class="photo" role="img" aria-label="Assorted hand tools and tape measure" style="background:linear-gradient(160deg,#ffffff,#eeeeee 45%,#c9a048 75%,#a83a2a)"></div>
    <div class="info">
      <h2>Equipment Maintenance</h2>
      <ul>
        <li><i class="tick"></i>Lorem ipsum dolor sit amet, consectetur adipisicing elit, sed do eiusmod tempor incididunt</li>
        <li><i class="tick"></i>Lorem ipsum dolor sit amet, consectetur adipisicing elit,</li>
        <li><i class="tick"></i>Lorem ipsum dolor sit amet, consectetur adipisicing elit, sed do eiusmod tempor incididunt</li>
        <li><i class="tick"></i>Sed do eiusmod tempor incididunt ut labore et dolore magna aliqua</li>
      </ul>
      <div class="ctas"><a class="btn btn-sm btn-green" href="#">Contact Sales ›</a><a class="btn btn-sm btn-grey" href="#">Read More ›</a></div>
    </div>
  </article>
  <article class="product">
    <div class="photo" role="img" aria-label="GPS survey rover on a tripod in a field" style="background:linear-gradient(180deg,#5f8fc4,#9ab8d8 55%,#a0854c 75%,#6a5530)"></div>
    <div class="info">
      <h2>GPS</h2>
      <ul>
        <li><i class="tick"></i>Lorem ipsum dolor sit amet, consectetur adipisicing elit, sed do eiusmod tempor incididunt</li>
        <li><i class="tick"></i>Lorem ipsum dolor sit amet, consectetur adipisicing elit,</li>
        <li><i class="tick"></i>Lorem ipsum dolor sit amet, consectetur adipisicing elit, sed do eiusmod tempor incididunt</li>
        <li><i class="tick"></i>Sed do eiusmod tempor incididunt ut labore et dolore magna aliqua</li>
      </ul>
      <div class="ctas"><a class="btn btn-sm btn-green" href="#">Contact Sales ›</a><a class="btn btn-sm btn-grey" href="#">Read More ›</a></div>
    </div>
  </article>
</main>

<a class="to-top" href="#">BACK<br>TO TOP</a>

<footer class="footer">
  <div class="footer-tab">TRBW</div>
  <div class="footer-cols">
    <div>
      <h3>Softwares</h3>
      <ul>
        <li>GroundQuote®</li><li class="active">SiteTrack®</li><li>Safety Application</li><li>Crew Dispatch</li><li>GPS</li><li>Fleet Circle</li><li>FuelLog Plus</li><li>bidrecord.example</li><li>Mobile Apps</li><li>Mobile Apps</li>
      </ul>
    </div>
    <div>
      <h3>Services</h3>
      <ul><li>Could Services</li><li>Custom Programming</li><li>Universities</li><li>Instant Support</li></ul>
      <h3 class="sub">Training &amp; Events</h3>
      <ul><li>Training Options</li><li>Dummy Links Plz Ad</li></ul>
    </div>
    <div>
      <h3>News</h3>
      <ul><li>Newsroom</li><li>Newsletter</li><li>Press Kit</li><li>Newsletter Subscription</li></ul>
      <h3 class="sub">Careers</h3>
      <ul><li>Careers At TRBW</li><li>Careers in Construction</li></ul>
    </div>
    <div>
      <h3>About Us</h3>
      <ul><li>About TRBW</li><li>TRBW Culture Blog</li><li>Our Clients</li><li>Contact/More Info</li><li>The TRBW Story</li><li>Map &amp; Directions</li><li>Stability</li><li>Why Choose TRBW</li></ul>
    </div>
    <div>
      <h3>Contact Us</h3>
      <ul class="contact">
        <li><b>Sales :</b>800 - 555 - 0195</li>
        <li><b>Support :</b>800 - 555 - 0196</li>
        <li><b>Email :</b>info@trbw.example</li>
        <li class="addr">4820 W. Quarry Blvd.<br>Stone Ridge, TX 77000</li>
      </ul>
      <h3 class="sub">Social Media</h3>
      <div class="social"><span></span><span></span><span></span><span></span><span></span><span></span></div>
    </div>
  </div>
</footer>

<div class="bottombar">
  <span>All Right Reserved © Copyright with www.trbw.example - 2012</span>
  <a href="#">Terms</a><a href="#">Privacy Policy</a>
</div>

</body>
</html>
```